Wordpress Web Design & Coding for velcorahealth.ca

We need a website for a new investment company that is visually grabbing and vibrant. We would like to see a web page that displays trust, growth and confidence. Needs to be responsive and mobile friendly for all browsers and coded for both Android & IOS.

Open to the number of pages and menu items. I selected 4 but if you feel the layout would work better with less I am open to this. Need to sell the people (management team/related businesses) and then show where the invested money will be going (upcoming projects).

Company Info:

Vel Cora is an investment company put together by a group of seasoned business professionals who have come together to combine decades of success in the real estate development, management, financing and medical services. The company will be a full service company offering turn key solutions for medical professionals.

Vel-Cora will focus on providing a full range of services via a group of distinct companies to deliver newly emerging needs of the medical community. The end goal will be to create complete solutions for individuals in the medical community. Our group has experience and success with the conceptualization, construction and financing of medical and dental clinic spaces. Vel-Cora Solutions will be established to accommodate all areas of the development and creation of clinics for medical professionals from building construction to equipment financing and administrations.

You can mention these companies and take photos from their websites. You can also use stock photos.

Our construction partner:
https://318bld.com/projects/

Our equipment leasing partner:
https://www.norvixa.com/

Our Management Team and medical partners

Gil Parish
https://www.ourfirmstance.ca/

Dietmar Vellasquin
https://www.gshdentalservices.com/about-us

PROPOSED PROJECTS (see attachment for details)
Pinegrove Business Park
Holtmere Business Park
Mt. Corwin Ridge Professional

Target Market(s)

Investors

Industry/Entity Type

Investment

Coding

Coded - Design and coding required

Number of Pages Required

4 page

Font styles to use
Sans Serif

Requirements
Must have
• Wordpress – must be both desktop and mobile friendly with fast page load speed
Ability to edit after ourselves in Wordpress
Attractive home page with logo etc.
Logo colours are: for the blue the pantone color is #0355a3
and for the green is #8cc63f

Sections, about us, what we do/services we provide, contact us

```html
<!DOCTYPE html>
<html lang="en">
<head>
<meta charset="utf-8">
<title>Vel-Cora Solutions</title>
<link href="https://fonts.googleapis.com/css2?family=Montserrat:wght@400;500;600;700&family=Roboto+Condensed:wght@700&display=swap" rel="stylesheet">
<style>
:root{
  --blue:#0355a3;
  --blue-dark:#0a4f9c;
  --green:#8cc63f;
  --text:#444b55;
  --muted:#7a828c;
  --pale:#eaf3fc;
  --white:#ffffff;
}
*{margin:0;padding:0;box-sizing:border-box}
html,body{width:1200px;height:3706px;overflow:hidden}
body{font-family:'Montserrat',sans-serif;color:var(--text);background:var(--white);position:relative}
.abs{position:absolute}
.blue{color:var(--blue)}
.green{color:var(--green)}

/* header */
.site-header{position:absolute;top:0;left:0;width:1200px;height:114px;background:var(--white);border-bottom:1px solid #e3e6ea}
.brand{position:absolute;left:144px;top:28px;display:flex;align-items:center;gap:10px}
.brand-mark{width:22px;height:22px;background:var(--blue)}
.brand-name{font-weight:700;font-size:26px;color:var(--blue);line-height:1;letter-spacing:.5px}
.brand-name small{display:block;font-size:15px;letter-spacing:2px;margin-top:4px}
.top-contact{position:absolute;right:142px;top:16px;display:flex;gap:18px;font-size:14px;font-weight:600;color:#222}
.top-contact span{display:flex;align-items:center;gap:8px}
.dot-icon{width:26px;height:26px;border-radius:50%;background:var(--green);display:flex;align-items:center;justify-content:center}
.main-nav{position:absolute;right:142px;top:72px;display:flex;gap:48px;font-size:13px;font-weight:700;color:#222;letter-spacing:.3px}
.main-nav .active{color:var(--blue);position:relative}
.main-nav .active:after{content:"";position:absolute;left:-4px;right:-4px;top:30px;height:3px;background:var(--blue)}

/* hero */
.hero{position:absolute;top:114px;left:0;width:1200px;height:459px;background:linear-gradient(100deg,#c9dcec 0%,#a9c7e2 35%,#7fb0da 65%,#4f8ec8 100%)}
.hero-copy{position:absolute;right:142px;top:146px;text-align:right;font-family:'Roboto Condensed',sans-serif;color:#111}
.hero-copy h1{font-family:'Montserrat',sans-serif;font-size:35px;font-weight:700;letter-spacing:1px;margin-bottom:8px}
.hero-copy p{font-size:18px;line-height:29px}
.btn{display:inline-block;background:var(--blue);color:var(--white);font-weight:700;border-radius:3px;text-align:center}
.hero .btn{position:absolute;right:0;top:261px;width:127px;height:41px;line-height:41px;font-size:15px;font-family:'Montserrat',sans-serif}

/* about */
.section-title{font-size:29px;font-weight:700;text-align:center;letter-spacing:.5px}
.about .section-title{position:absolute;top:643px;width:1200px}
.about-text{position:absolute;top:703px;left:150px;width:900px;text-align:center;font-size:12.5px;line-height:23px}
.about-text p+p{margin-top:8px}
.about-text u{color:var(--blue)}
.about .btn{position:absolute;left:537px;top:872px;width:126px;height:34px;line-height:34px;font-size:14px}

/* solutions */
.solution-band{position:absolute;top:978px;left:0;width:1200px;height:219px;background:var(--green)}
.solution-band h2{position:absolute;top:70px;width:1200px;text-align:center;color:var(--white);font-size:30px;font-weight:700;letter-spacing:.5px}
.rule{display:block;width:38px;height:3px;background:var(--white);margin:12px auto 0}
.rule.blue-rule{background:#b9d3ec}
.service{position:absolute;top:1127px;width:423px}
.service .ph{width:423px;height:457px;border-radius:6px}
.service h3{margin-top:22px;font-size:20px;color:var(--blue);font-weight:700;padding-left:2px}
.service p{margin-top:16px;font-size:12.5px;line-height:23px;padding-left:2px}
.service a{display:block;margin-top:10px;color:var(--green);font-weight:600;font-size:15px;padding-left:5px}

/* projects */
.projects .section-title{position:absolute;top:1820px;width:1200px}
.feature{position:absolute;left:141px;top:1895px;width:446px}
.feature .ph{height:304px}
.feature h3{margin-top:14px;font-size:19px;color:var(--blue);font-weight:700}
.feature .sub{font-size:12.5px;color:var(--muted);margin-top:2px}
.feature p{font-size:12.5px;line-height:23px;margin-top:12px;letter-spacing:.2px}
.meta{display:flex;justify-content:space-between;font-size:11px;color:#555;border-top:1px solid #e4e4e4;padding-top:10px;margin-top:10px}
.meta i{font-style:normal;color:var(--green)}
.post{position:absolute;left:606px;width:453px;height:143px}
.post .ph{position:absolute;left:0;top:0;width:213px;height:143px}
.post .body{position:absolute;left:234px;top:16px;width:219px}
.post h4{font-size:14.5px;color:var(--blue);font-weight:700}
.post .sub{font-size:12px;color:var(--muted);margin-top:4px}
.post p{font-size:11.5px;line-height:18px;margin-top:4px;letter-spacing:.6px}
.post .meta{border:none;padding-top:0;margin-top:10px}
.arrow{position:absolute;top:2118px;width:32px;height:32px;border-radius:50%;background:#eeeeee;display:flex;align-items:center;justify-content:center}

/* partners */
.people{position:absolute;top:2446px;left:0;width:1200px;height:593px;background:var(--pale)}
.people h2{position:absolute;top:62px;font-size:29px;font-weight:700;line-height:37px;letter-spacing:.5px}
.people h2:after{content:"";display:block;width:38px;height:3px;background:#b9d3ec;margin-top:16px}
.card{position:absolute;top:176px;width:208px}
.card .ph{height:217px}
.card .label{height:56px;background:var(--blue);color:var(--white);font-weight:700;font-size:16px;text-align:center;display:flex;align-items:center;justify-content:center;line-height:21px}
.card .partner-name{margin-top:22px;text-align:center;font-size:17px;color:#6b7078;font-weight:500;letter-spacing:1px}

/* newsletter */
.newsletter h2{position:absolute;top:3107px;width:1200px;text-align:center;font-size:31px;font-weight:700;letter-spacing:.5px}
.newsletter .lead{position:absolute;top:3172px;width:1200px;text-align:center;font-size:14px;line-height:19px;color:#222}
.newsletter .lead span{color:var(--blue)}
.newsletter .field{position:absolute;left:311px;top:3219px;width:452px;height:41px;border:1px solid #cfd4da;border-radius:3px;font-size:12px;color:#777;padding:13px 15px}
.newsletter .btn{position:absolute;left:776px;top:3219px;width:112px;height:41px;line-height:41px;font-size:14px}

/* footer */
.site-footer{position:absolute;top:3332px;left:0;width:1200px;height:320px;background:var(--blue-dark);color:var(--white)}
.fcol{position:absolute;top:70px}
.fcol h5{color:var(--green);font-size:13px;font-weight:700;letter-spacing:.3px;margin-bottom:24px}
.fcol ul{list-style:none;font-size:11.5px;line-height:22px}
.fcol ul li:before{content:"» ";color:#cfe0f2}
.divider{position:absolute;top:70px;width:1px;height:190px;background:rgba(255,255,255,.25)}
.contact-row{display:flex;gap:12px;margin-bottom:18px;font-size:12px;line-height:19px}
.contact-row b{font-weight:700;font-size:12px}
.circ{width:28px;height:28px;border-radius:50%;flex:none;display:flex;align-items:center;justify-content:center}
.circ.g{background:var(--green)}
.circ.w{background:var(--white)}
.social{display:flex;align-items:center;gap:12px;font-size:13px;margin-bottom:15px}
.foot-brand{position:absolute;left:878px;top:96px;text-align:center;color:#cfe0f2;font-weight:700;font-size:36px;line-height:1;letter-spacing:1px}
.foot-brand small{display:block;font-size:20px;letter-spacing:3px;margin-top:6px}
.foot-brand .sq{width:28px;height:28px;background:#cfe0f2;margin:0 auto 12px}
.copyright{position:absolute;top:3652px;left:0;width:1200px;height:54px;background:var(--green);color:var(--white);font-size:13px;text-align:center;line-height:54px}
.copyright b{font-weight:700}
</style>
</head>
<body>

<header class="site-header">
  <div class="brand">
    <div class="brand-mark"></div>
    <div class="brand-name">VEL-CORA<small>SOLUTIONS</small></div>
  </div>
  <div class="top-contact">
    <span><span class="dot-icon"><svg width="13" height="13" viewBox="0 0 24 24"><path fill="#fff" d="M6.6 10.8a15.1 15.1 0 0 0 6.6 6.6l2.2-2.2c.3-.3.7-.4 1-.2 1.1.4 2.3.6 3.6.6.6 0 1 .4 1 1V20c0 .6-.4 1-1 1A17 17 0 0 1 3 4c0-.6.4-1 1-1h3.5c.6 0 1 .4 1 1 0 1.3.2 2.5.6 3.6.1.3 0 .7-.2 1z"/></svg></span>604.555.0182</span>
    <span><span class="dot-icon"><svg width="13" height="13" viewBox="0 0 24 24"><path fill="none" stroke="#fff" stroke-width="2.4" d="M3 6h18v12H3zM3 6l9 7 9-7"/></svg></span>support@velcorasol.com</span>
  </div>
  <nav class="main-nav">
    <span class="active">HOME</span><span>ABOUT US</span><span>WHAT WE DO</span><span>CONTACT US</span>
  </nav>
</header>

<section class="hero" role="img" aria-label="Doctor in a white coat touching a glowing digital interface">
  <div class="hero-copy">
    <h1>VEL-CORA</h1>
    <p>Is An Investment Company With Focus on<br>Providing A Full Range of Services, For The Newly<br>Emerging Needs of The Medical Community</p>
    <span class="btn">Know More</span>
  </div>
</section>

<section class="about">
  <h2 class="section-title"><span class="blue">ABOUT</span> <span class="green">VEL-CORA SOLUTIONS</span></h2>
  <div class="about-text">
    <p><u>Vel-Cora</u> is an investment company put together by a group of seasoned business professionals who have come together to combine decades of success in the real estate development, management, financing and medical services. The company will be a full service company offering turnkey solutions for medical professionals.</p>
    <p>Vel-Cora will focus on providing a full range of services via a group of distinct companies to deliver newly emerging needs of the medical community. The end goal will be to create complete solutions for individuals in the medical community. Our group has experience and success with the conceptualization, construction and financing of medical and dental clinic spaces.</p>
  </div>
  <span class="btn">Read More</span>
</section>

<section class="solutions">
  <div class="solution-band"><h2>VEL-CORA SOLUTION<span class="rule"></span></h2></div>
  <article class="service" style="left:141px">
    <div class="ph" role="img" aria-label="Hand touching a hexagon grid of business icons labelled leasing" style="background:linear-gradient(135deg,#dfe9f4,#7aa3cf 55%,#2c5f9a)"></div>
    <h3>LEASING OPERATIONS</h3>
    <p>Vel-Cora Solutions leasing divison will secure an investment portfolio comprised of equipment leases and other small business financing solutions across Western Canada.</p>
    <a>Know More ➔</a>
  </article>
  <article class="service" style="left:635px">
    <div class="ph" role="img" aria-label="Open hand holding a glowing security shield over a network mesh" style="background:radial-gradient(circle at 50% 45%,#4f86c4,#0e3565 70%,#071f40)"></div>
    <h3>SECURITY MEASURES</h3>
    <p>Vel-Cora Solution leasing divison will implement a number of security measures which ensures investors are secure and returns are maximised over the elife of the investments.</p>
    <a>Know More ➔</a>
  </article>
</section>

<section class="projects">
  <h2 class="section-title"><span class="blue">UPCOMING</span> <span class="green">PROJECTS</span><span class="rule blue-rule"></span></h2>
  <div class="arrow" style="left:85px"><svg width="10" height="10" viewBox="0 0 10 10"><path d="M7 1 3 5l4 4" fill="none" stroke="#333" stroke-width="1.8"/></svg></div>
  <div class="arrow" style="left:1082px"><svg width="10" height="10" viewBox="0 0 10 10"><path d="M3 1l4 4-4 4" fill="none" stroke="#333" stroke-width="1.8"/></svg></div>
  <article class="feature">
    <div class="ph" role="img" aria-label="Empty bright industrial warehouse interior" style="background:linear-gradient(180deg,#6f8fb8,#b9cde4 50%,#e9f0f8)"></div>
    <h3>Pinegrove Business Park</h3>
    <div class="sub">Office and Light Industrial Building Project</div>
    <p>The Pinegrove Business Park in Langford, British Columbia on Vaancouver island, is presently under contract with partners that are controlled by individuals who form part of the...(+)</p>
    <div class="meta"><span><i>▦</i> Apr 10, 2020</span><span><i>○</i> 3 Comments</span></div>
  </article>
  <article class="post" style="top:1895px">
    <div class="ph" role="img" aria-label="Historic stone civic building facade" style="background:linear-gradient(180deg,#a9c4de,#c2b7a5 55%,#6f6353)"></div>
    <div class="body"><h4>Holtmere Business Park</h4><p>The city of Langford is a core municipalty in the Western Communities. It is currently...(+)</p><div class="meta"><span><i>▦</i> Apr 10, 2020</span><span><i>○</i> 3 Comments</span></div></div>
  </article>
  <article class="post" style="top:2062px">
    <div class="ph" role="img" aria-label="Silhouettes of business people over a city skyline" style="background:linear-gradient(180deg,#cfe1f2,#5f8dbd 60%,#1f4f85)"></div>
    <div class="body" style="top:6px"><h4>Mt. Corwin Ridge Professional</h4><div class="sub">Professional Services Buildings</div><p>Mt. Corwin Ridge Professional building will feature a repurposed building adjacent to Mt.Corwin Ridge in...(+)</p><div class="meta"><span><i>▦</i> Apr 10, 2020</span><span><i>○</i> 3 Comments</span></div></div>
  </article>
  <article class="post" style="top:2230px">
    <div class="ph" role="img" aria-label="Colleagues talking at a meeting table" style="background:linear-gradient(135deg,#e6e3df,#9a8b7d 55%,#3c3a3a)"></div>
    <div class="body"><h4>Lorem Ipsum Dolor</h4><p>Lorem ipsum dolor sit amn alamet commons consectetuer adipiscing elit lorem ipsum amet dolar... (+)</p><div class="meta"><span><i>▦</i> Apr 10, 2020</span><span><i>○</i> 3 Comments</span></div></div>
  </article>
</section>

<section class="people">
  <h2 style="left:143px"><span class="blue">OUR</span><br><span class="green">PARTNERS</span></h2>
  <h2 style="left:628px"><span class="blue">OUR MANAGEMENT TEAM</span><br><span class="green">AND MEDICAL PARTNERS</span></h2>
  <div class="card" style="left:141px">
    <div class="ph" role="img" aria-label="White commercial building exterior" style="background:linear-gradient(180deg,#8fb5dc,#e8ecef 55%,#7b8a5c)"></div>
    <div class="label">Construction<br>Partner</div>
    <div class="partner-name">318 BUILDERS INC.</div>
  </div>
  <div class="card" style="left:367px">
    <div class="ph" role="img" aria-label="Modern white professional office building" style="background:linear-gradient(180deg,#cfe0ef,#f2f4f6 55%,#8c939a)"></div>
    <div class="label">Equipment<br>Leasing Partner</div>
    <div class="partner-name">NORVIXA</div>
  </div>
  <div class="card" style="left:624px">
    <div class="ph" role="img" aria-label="Portrait of a physician in a white coat" style="background:linear-gradient(180deg,#5a5a5a,#9a9a9a 60%,#e6e6e6)"></div>
    <div class="label">Gil Parish</div>
    <div class="partner-name">firmstance</div>
  </div>
  <div class="card" style="left:850px">
    <div class="ph" role="img" aria-label="Portrait of a man in a cap outdoors by the sea" style="background:linear-gradient(180deg,#d6e3ea,#6f9bb0 55%,#3d6475)"></div>
    <div class="label">Dietmar<br>Vellasquin</div>
    <div class="partner-name">GSH DENTAL</div>
  </div>
</section>

<section class="newsletter">
  <h2><span class="blue">SUBSCRIBE TO</span> <span class="green">OUR NEWSLETTER</span></h2>
  <div class="lead">Want to keep up to date with all our latest news and information?<br><span>Enter your email below to be added to our mailing list.</span></div>
  <div class="field">Enter your email address</div>
  <span class="btn">SUBSCRIBE</span>
</section>

<footer class="site-footer">
  <div class="fcol" style="left:144px">
    <h5>QUICK LINKS</h5>
    <ul><li>HOME</li><li>ABOUT US</li><li>WHAT WE DO</li><li>CONTACT US</li></ul>
  </div>
  <div class="divider" style="left:288px"></div>
  <div class="fcol" style="left:340px">
    <h5>CONTACT DETAILS</h5>
    <div class="contact-row"><span class="circ g"><svg width="12" height="14" viewBox="0 0 12 16"><path fill="#fff" d="M6 0a6 6 0 0 0-6 6c0 4.5 6 10 6 10s6-5.5 6-10a6 6 0 0 0-6-6zm0 8.5A2.5 2.5 0 1 1 6 3.5a2.5 2.5 0 0 1 0 5z"/></svg></span><div><b>VEL-CORA SOLUTION</b><br>123, Building Name, Street<br>City, State 123456</div></div>
    <div class="contact-row"><span class="circ g"><svg width="13" height="13" viewBox="0 0 24 24"><path fill="#fff" d="M6.6 10.8a15.1 15.1 0 0 0 6.6 6.6l2.2-2.2c.3-.3.7-.4 1-.2 1.1.4 2.3.6 3.6.6.6 0 1 .4 1 1V20c0 .6-.4 1-1 1A17 17 0 0 1 3 4c0-.6.4-1 1-1h3.5c.6 0 1 .4 1 1 0 1.3.2 2.5.6 3.6.1.3 0 .7-.2 1z"/></svg></span><div><b>Phone</b><br>604.555.0182</div></div>
    <div class="contact-row"><span class="circ g"><svg width="13" height="13" viewBox="0 0 16 16"><path fill="#fff" d="M4 1h8v4H4zM1 6h14v6h-3v3H4v-3H1zm4 4v4h6v-4z"/></svg></span><div><b>Fax</b><br>support@velcorasol.com</div></div>
  </div>
  <div class="divider" style="left:615px"></div>
  <div class="fcol" style="left:663px">
    <h5>FOLLOW US ON</h5>
    <div class="social"><span class="circ w"></span>Friendwall</div>
    <div class="social"><span class="circ w"></span>Chirpline</div>
    <div class="social"><span class="circ w"></span>Workedge</div>
  </div>
  <div class="foot-brand" style="width:181px"><div class="sq"></div>VEL-CORA<small>SOLUTIONS</small></div>
</footer>
<div class="copyright">Copyright © 2020 <b>VEL-CORA SOLUTION</b>. All Rights Reserved.</div>

</body>
</html>
```